We are a recruitment company based in Norwich/Cambridge England.
I have included our company logo which we want to remain the same.

What we are looking for is a new creative Business card which will really stand out!!

Contact Information for Business Card

Harriet Dunmore
email: Harriet@plavex.co.uk
Address: Brackwell House
Fenmoor Enterprise Park
Partridge Way
Norwich
QB9 3KX
Tel:01632 960418

```html
<!DOCTYPE html>
<html lang="en">
<head>
<meta charset="utf-8">
<title>Plavex Business Card</title>
<link href="https://fonts.googleapis.com/css2?family=Roboto:wght@400;500;700&display=swap" rel="stylesheet">
<style>
  :root {
    --backdrop: #2b2623;
    --card: #1d1f21;
    --green: #7dc242;
    --grey: #9b9b9e;
    --white: #f2f2f2;
    --rule: #8a8a8a;
  }
  * { box-sizing: border-box; margin: 0; padding: 0; }
  html, body { width: 1200px; height: 769px; overflow: hidden; }
  body {
    background: var(--backdrop);
    font-family: "Roboto", sans-serif;
    position: relative;
  }
  .card {
    position: absolute;
    top: 230px;
    width: 520px;
    height: 300px;
    background: var(--card);
    border-radius: 3px;
    box-shadow: 0 10px 30px rgba(0,0,0,.45);
  }
  .card--front { left: 50px; }
  .card--back { left: 630px; }

  /* Front */
  .brand {
    position: absolute;
    left: 0; right: 0; top: 100px;
    display: flex; justify-content: center; align-items: center; gap: 14px;
  }
  .brand__dot { width: 40px; height: 40px; border-radius: 50%; background: var(--green); }
  .brand__name { font-size: 46px; font-weight: 700; color: var(--green); letter-spacing: -.5px; }
  .tagline {
    position: absolute; left: 0; right: 0; top: 160px;
    text-align: center; font-size: 10px; color: var(--grey); letter-spacing: 2px;
  }
  .front-web {
    position: absolute; left: 0; right: 0; bottom: 55px;
    text-align: center; font-size: 13px; color: var(--grey); letter-spacing: 7px;
  }

  /* Back */
  .mark {
    position: absolute; left: 40px; top: 70px; width: 190px; height: 160px;
    display: flex; flex-direction: column; align-items: center; justify-content: center; gap: 12px;
  }
  .mark__dot { width: 110px; height: 110px; border-radius: 50%; background: var(--green); }
  .mark__name { font-size: 22px; font-weight: 700; color: var(--green); }
  .divider {
    position: absolute; left: 255px; top: 40px; width: 1px; height: 220px;
    background: var(--rule);
  }
  .contact { position: absolute; left: 278px; top: 48px; width: 230px; }
  .contact__name { font-size: 19px; font-weight: 700; color: var(--green); text-transform: uppercase; }
  .contact__role { font-size: 13px; font-weight: 500; color: var(--grey); text-transform: uppercase; margin-bottom: 10px; }
  .contact__address { font-size: 12px; color: var(--white); line-height: 1.35; margin-bottom: 8px; }
  .contact__list { list-style: none; }
  .contact__item { display: flex; align-items: center; gap: 8px; font-size: 12.5px; color: var(--white); line-height: 1.55; }
  .contact__item svg { width: 12px; height: 12px; flex: none; fill: var(--green); }
</style>
</head>
<body>
  <section class="card card--front">
    <div class="brand"><span class="brand__dot"></span><span class="brand__name">Plavex</span></div>
    <p class="tagline">Technology Recruitment</p>
    <p class="front-web">www.plavex.co.uk</p>
  </section>

  <section class="card card--back">
    <div class="mark"><span class="mark__dot"></span><span class="mark__name">Plavex</span></div>
    <div class="divider"></div>
    <div class="contact">
      <p class="contact__name">Harriet Dunmore</p>
      <p class="contact__role">CEO/Founder</p>
      <p class="contact__address">Brackwell House<br>Fenmoor Enterprise Park<br>Partridge Way, Norwich QB9 3KX</p>
      <ul class="contact__list">
        <li class="contact__item"><svg viewBox="0 0 12 12"><path d="M2.5 0.5l2 2.5-1.2 1.4c.7 1.5 1.9 2.7 3.3 3.3L8 6.5l2.5 2-1 2.5C5 11 1 7 .5 2.5z"/></svg>01632 960418</li>
        <li class="contact__item"><svg viewBox="0 0 12 12"><path d="M3 0h6v12H3zM4 1.5v8h4v-8z"/></svg>01632 960527</li>
        <li class="contact__item"><svg viewBox="0 0 12 12"><path d="M3 0h6v3H3zM1 4h10v5H9v3H3V9H1zM4 8v3h4V8z"/></svg>01632 960733</li>
        <li class="contact__item"><svg viewBox="0 0 12 12"><path d="M0 2h12v8H0zM1 3l5 3.5L11 3z" fill-rule="evenodd"/></svg>Harriet@plavex.co.uk</li>
        <li class="contact__item"><svg viewBox="0 0 12 12"><circle cx="6" cy="6" r="6"/></svg>www.plavex.co.uk</li>
      </ul>
    </div>
  </section>
</body>
</html>
```